Our companies name is The Gilded Ladle and we specialize in craft cupcakes, what I mean by that is that we bake our cupcakes with craft beer and other alcoholic drinks. We are trying to focus on being elegant but at the same time unpretentious. Since we are incorporating beer in our cupcakes we want the business card to have our logo in the front and our information in the back.

Once we select the best design we will provide the contact information to be added. Thank you.

Industry/Entity Type

Business

Font styles to use
Decorative
Script

Requirements
Must have
• Round corners
Should not have
• Square corners

```html
<!DOCTYPE html>
<html lang="en">
<head>
<meta charset="utf-8">
<title>The Gilded Ladle – Business Card</title>
<link rel="stylesheet" href="https://fonts.googleapis.com/css2?family=Alfa+Slab+One&family=Arimo:wght@400&display=swap">
<style>
  :root {
    --red: #e8202f;
    --black: #0b0b0b;
    --white: #ffffff;
    --backdrop: #d9d6d2;
    --ink-light: #f2f2f2;
  }
  html, body {
    margin: 0;
    padding: 0;
    width: 1200px;
    height: 1023px;
    overflow: hidden;
    background: var(--backdrop);
  }
  .canvas {
    position: relative;
    width: 1200px;
    height: 1023px;
  }
  .card {
    position: absolute;
    left: 250px;
    width: 700px;
    height: 400px;
    border-radius: 24px;
    overflow: hidden;
    background: var(--white);
    box-shadow: 0 6px 18px rgba(0,0,0,0.18);
  }
  .card--back { top: 70px; }
  .card--front { top: 553px; }
  .card svg.card-shapes {
    position: absolute;
    inset: 0;
    width: 700px;
    height: 400px;
  }
  .holder {
    position: absolute;
    left: 36px;
    top: 52px;
    width: 330px;
    color: var(--white);
  }
  .holder-name {
    font-family: "Alfa Slab One", Georgia, serif;
    font-size: 32px;
    letter-spacing: 1px;
    margin: 0;
  }
  .holder-role {
    font-family: "Arimo", Arial, sans-serif;
    font-size: 17px;
    margin: 6px 0 0 2px;
  }
  .contact {
    position: absolute;
    left: 428px;
    top: 112px;
    width: 250px;
    font-family: "Arimo", Arial, sans-serif;
    font-size: 16px;
    line-height: 1.65;
    color: var(--ink-light);
    margin: 0;
    list-style: none;
    padding: 0;
  }
  .brand {
    position: absolute;
    display: flex;
    align-items: center;
    gap: 12px;
  }
  .brand-dot {
    width: 22px;
    height: 22px;
    border-radius: 50%;
    background: var(--red);
    flex: none;
  }
  .brand-name {
    font-family: "Alfa Slab One", Georgia, serif;
    color: var(--black);
    margin: 0;
  }
  .card--back .brand { left: 60px; top: 290px; }
  .card--back .brand-name { font-size: 28px; }
  .card--front .brand { left: 0; right: 0; top: 170px; justify-content: center; }
  .card--front .brand-name { font-size: 40px; }
</style>
</head>
<body>
<main class="canvas">

  <section class="card card--back" aria-label="Card back with contact details">
    <svg class="card-shapes" viewBox="0 0 700 400" aria-hidden="true">
      <rect class="panel-contact" x="400" y="0" width="300" height="400" fill="var(--black)"/>
      <polygon class="panel-name" points="0,0 400,0 400,180 200,230 0,180" fill="var(--red)"/>
      <polyline points="0,180 200,230 400,180" fill="none" stroke="var(--black)" stroke-width="5"/>
    </svg>
    <div class="holder">
      <h1 class="holder-name">EMPLOYEE NAME</h1>
      <p class="holder-role">Managing Director</p>
    </div>
    <ul class="contact">
      <li>C : xxx xxx xxxx</li>
      <li>T : (xxx) xxx-xxxx</li>
      <li>W : www.yourwebsit.com</li>
      <li>E : info@youremail.com</li>
      <li>Your Address Inc 2nd Lane Ave<br>Brookfield, ST 00000</li>
    </ul>
    <div class="brand">
      <span class="brand-dot"></span>
      <p class="brand-name">The Gilded Ladle</p>
    </div>
  </section>

  <section class="card card--front" aria-label="Card front with brand name">
    <svg class="card-shapes" viewBox="0 0 700 400" aria-hidden="true">
      <polygon class="wedge-top" points="0,0 700,0 350,110" fill="var(--black)"/>
      <polyline points="0,0 350,110 700,0" fill="none" stroke="var(--red)" stroke-width="5"/>
      <polygon class="wedge-bottom" points="0,400 700,400 350,290" fill="var(--black)"/>
      <polyline points="0,400 350,290 700,400" fill="none" stroke="var(--red)" stroke-width="5"/>
    </svg>
    <div class="brand">
      <span class="brand-dot"></span>
      <p class="brand-name">The Gilded Ladle</p>
    </div>
  </section>

</main>
</body>
</html>
```